Kestal-Materials. Limestone; improving the world

New Limestone company and need logo design.
Limestone offsets carbon mitigation industries restore and replenish soil fertilities in the Prairies, the breadbasket of the world. At the same time, Limestone is proving a critical emergent component of carbon capture sequestration technology will therefore play a critical role in the development of the western Canadian energy industries
Our limestone resources are situated in the foothills of the Canadian Rockies well-positioned above the sprawling fields of the vast peace district.
Agriculture and oli sites
Kestal Materials
3 page

```html
<!DOCTYPE html>
<html lang="en">
<head>
<meta charset="utf-8">
<title>Kestal Materials</title>
<link href="https://fonts.googleapis.com/css2?family=Oswald:wght@500;600&family=Roboto:ital,wght@0,400;0,500;0,700;1,500&display=swap" rel="stylesheet">
<style>
:root{
  --green:#7dbd3a;
  --blue:#3aa0d1;
  --ink:#111;
  --text:#555;
  --muted:#777;
  --panel:#f4f4f4;
  --white:#fff;
  --footer:#000;
}
*{box-sizing:border-box;margin:0;padding:0}
html,body{width:1200px;height:3889px;overflow:hidden}
body{position:relative;font-family:'Roboto',sans-serif;color:var(--text);background:var(--white)}
.abs{position:absolute}
.display{font-family:'Oswald',sans-serif;font-weight:500;color:var(--ink);text-transform:uppercase}
.btn{position:absolute;display:flex;align-items:center;justify-content:center;background:var(--blue);color:var(--white);font-weight:500;font-size:16px;text-transform:uppercase}
.copy{font-size:13.5px;line-height:24px;color:var(--text)}

/* hero */
.hero{left:0;top:0;width:1200px;height:569px;background:linear-gradient(160deg,#6aab2e 0%,#4f9223 45%,#6ab234 100%)}
.hero-globe{left:820px;top:140px;width:230px;height:429px;border-radius:115px 115px 0 0;background:linear-gradient(180deg,#7fa7a6 0%,#5d8d71 45%,#7fa0b7 100%);opacity:.9}
.brand{left:99px;top:22px;font-size:25px;font-weight:700;color:var(--white);letter-spacing:.3px}
.nav{left:663px;top:26px;display:flex;font-size:15px;font-weight:500;color:var(--white)}
.nav span{padding:0 19px}
.hero-title{left:99px;top:210px;font-size:56px;color:var(--white)}
.hero-sub{left:100px;top:285px;font-size:21px;color:var(--white)}
.hero-arrow{top:270px}
.dots{left:560px;top:532px;display:flex;gap:10px}
.dots i{width:12px;height:12px;border:1.5px solid var(--white);border-radius:50%}
.dots i.on{background:var(--white)}

/* solutions */
.solutions-bg{left:0;top:569px;width:1200px;height:439px;background:var(--panel)}
.section-title{width:1200px;left:0;text-align:center;font-size:40px}
.card{width:321px;height:357px;top:724px;background:var(--white);border-bottom:3px solid var(--blue);box-shadow:0 4px 18px rgba(0,0,0,.07);text-align:center;padding:42px 20px 0}
.card svg{display:block;margin:0 auto 12px}
.card h3{width:240px;margin:0 auto 14px;font-size:20px;font-weight:400;color:var(--ink);line-height:26px}
.card p{font-size:12.5px;line-height:24px;color:var(--muted)}
.rule{left:0;top:1141px;width:1200px;height:1px;background:#e6e6e6}
.round{width:36px;height:36px;border-radius:50%;background:var(--green);top:1123px;display:flex;align-items:center;justify-content:center}

/* who */
.who-head{left:101px;top:1327px;width:470px;font-size:35px;font-weight:500;color:var(--ink);line-height:42px}
.who-photo{left:599px;top:1337px;width:502px;height:330px;background:linear-gradient(120deg,#c9cdd3 0%,#8e98a4 50%,#4d5866 100%)}
.bubble{left:744px;top:1540px;width:286px;height:286px;border-radius:50%;background:var(--green);color:var(--white);text-align:center;padding:90px 28px 0;font-size:12.5px;font-style:italic;font-weight:500;line-height:18px}
.avatar{left:641px;top:1640px;width:64px;height:64px;border-radius:50%;background:linear-gradient(#9aa3ab,#5c6670);border:3px solid var(--white)}
.person{left:600px;top:1712px;width:150px;text-align:center;font-size:11px;line-height:14px;color:var(--text)}
.person b{display:block;font-size:13px;color:var(--ink);margin-bottom:3px}

/* sustainability */
.sus-bg{left:0;top:1909px;width:1200px;height:578px;background:var(--panel)}
.sus-img{left:104px;top:1977px;width:486px;height:436px;background:radial-gradient(circle at 50% 50%,#5f9a2c 0%,#8fae5c 35%,#e3d6c0 70%,#d8cab2 100%)}

/* lime */
.lime{left:0;top:2487px;width:1200px;height:444px;background:linear-gradient(180deg,#4a9ccb 0%,#5aaed6 100%)}
.lime-copy{left:170px;top:2664px;width:860px;text-align:center;color:var(--white);font-size:16px;font-weight:500;line-height:32px}
.outline-btn{left:504px;top:2771px;width:173px;height:48px;border:2px solid var(--white);color:var(--white);font-size:16px;font-weight:500;display:flex;align-items:center;justify-content:center}

/* news */
.news{top:3069px;width:324px;height:397px;background:var(--white);box-shadow:0 4px 18px rgba(0,0,0,.08)}
.news .img{height:216px;position:relative}
.news .date{position:absolute;left:0;bottom:0;background:var(--blue);color:var(--white);font-size:11px;padding:6px 12px}
.news h4{font-size:18px;font-weight:500;color:var(--ink);margin:19px 10px 8px}
.news p{font-size:12.5px;line-height:27px;color:var(--text);margin:0 10px}
.news a{display:block;margin:8px 12px;font-size:12px;font-weight:700;color:var(--blue);text-decoration:underline}

/* footer */
.footer{left:0;top:3540px;width:1200px;height:349px;background:var(--footer)}
.f-brand{left:100px;top:3625px;font-size:19px;font-weight:700;color:var(--white)}
.social{top:3677px;width:32px;height:32px;border-radius:50%;background:var(--white)}
.f-head{top:3620px;font-size:15px;font-weight:500;color:var(--white)}
.f-head::after{content:"";display:block;width:50px;height:2px;background:var(--blue);margin-top:10px}
.f-links{left:380px;top:3667px;font-size:13px;line-height:28px;color:var(--white)}
.f-contact{left:552px;font-size:13px;display:flex;align-items:flex-start;gap:12px;line-height:22px;color:var(--white)}
.f-contact i{width:26px;height:26px;border-radius:50%;background:#333;display:flex;align-items:center;justify-content:center;flex:none}
.f-sub{left:825px;top:3664px;font-size:12.5px;line-height:28px;width:260px;color:var(--white)}
.email{left:825px;top:3741px;width:267px;height:47px;background:var(--white);display:flex;align-items:center;padding-left:18px;color:#777;font-size:13px}
.send{left:1042px;top:3741px;width:50px;height:47px;background:var(--blue);display:flex;align-items:center;justify-content:center}
.f-rule{left:106px;top:3838px;width:985px;height:1px;background:#444}
.f-legal{top:3855px;font-size:12px;color:var(--white)}
</style>
</head>
<body>

<!-- hero -->
<section class="abs hero" role="img" aria-label="Green grass field with a child holding a globe overhead"></section>
<div class="abs hero-globe" role="img" aria-label="Child holding the Earth"></div>
<div class="abs brand">KESTAL MATERIALS</div>
<nav class="abs nav"><span>HOME</span><span>|</span><span>ABOUT</span><span>|</span><span>FAQ</span><span>|</span><span>CONTACT US</span></nav>
<h1 class="abs display hero-title">Kestal Materials</h1>
<p class="abs hero-sub">A global leader in lime and &nbsp;Limestone improving the world</p>
<div class="btn" style="left:101px;top:332px;width:186px;height:50px;font-size:15px">GET STARTED</div>
<svg class="abs hero-arrow" style="left:64px" width="20" height="40" viewBox="0 0 20 40"><path d="M18 2 2 20l16 18" fill="none" stroke="#fff" stroke-width="1.5"/></svg>
<svg class="abs hero-arrow" style="left:1112px" width="20" height="40" viewBox="0 0 20 40"><path d="M2 2l16 18L2 38" fill="none" stroke="#fff" stroke-width="1.5"/></svg>
<div class="abs dots"><i class="on"></i><i></i><i></i><i></i></div>

<!-- solutions -->
<div class="abs solutions-bg"></div>
<h2 class="abs display section-title" style="top:646px">Our Solutions</h2>

<div class="abs card" style="left:100px">
  <svg width="78" height="78" viewBox="0 0 78 78" fill="none" stroke="#3aa0d1" stroke-width="2.5"><circle cx="36" cy="38" r="30"/><circle cx="36" cy="38" r="22"/><path d="M36 22v16l10 6"/><circle cx="58" cy="58" r="10"/><circle cx="58" cy="58" r="4"/></svg>
  <h3>THE STANDARD LOREM IPSUM</h3>
  <p>Sed ut perspiciatis unde oatus uptatem acantium doloremque laudantium, totam m aperiam, eapsa quae ab illo inventore veritatis et quasi aro beatae vitae dicta plicabo. Nemo enim ipsam voluptatem quia voluptas sit aspernatur aut odit</p>
</div>
<div class="abs card" style="left:443px">
  <svg width="78" height="78" viewBox="0 0 78 78" fill="none" stroke="#3aa0d1" stroke-width="2.5"><path d="M39 4v22M30 13l9-9 9 9M18 16v22M10 24l8-8 8 8M60 16v22M52 24l8-8 8 8"/><circle cx="39" cy="42" r="8"/><path d="M24 76V62c0-6 6-10 15-10s15 4 15 10v14M8 76V56M70 76V56"/></svg>
  <h3>THE STANDARD LOREM IPSUM</h3>
  <p>Sed ut perspiciatis unde oatus uptatem acantium doloremque laudantium, totam m aperiam, eapsa quae ab illo inventore veritatis et quasi aro beatae vitae dicta plicabo. Nemo enim ipsam voluptatem quia voluptas sit aspernatur aut odit</p>
</div>
<div class="abs card" style="left:786px">
  <svg width="78" height="78" viewBox="0 0 78 78" fill="none" stroke="#3aa0d1" stroke-width="2.5"><circle cx="44" cy="44" r="26"/><circle cx="44" cy="44" r="18"/><path d="M44 32v12l8 6M38 8h12M44 8v10M4 34h14M8 44h10M4 54h14"/></svg>
  <h3>THE STANDARD LOREM IPSUM</h3>
  <p>Sed ut perspiciatis unde oatus uptatem acantium doloremque laudantium, totam m aperiam, eapsa quae ab illo inventore veritatis et quasi aro beatae vitae dicta plicabo. Nemo enim ipsam voluptatem quia voluptas sit aspernatur aut odit</p>
</div>
<div class="abs card" style="left:1129px">
  <svg width="78" height="78" viewBox="0 0 78 78"></svg>
  <h3>THE STANDARD LOREM IPSUM</h3>
  <p>Sed ut perspiciatis unde oatus uptatem acantium doloremque laudantium, totam m aperiam, eapsa quae ab illo inventore veritatis et quasi aro beatae vitae dicta plicabo. Nemo enim ipsam voluptatem quia voluptas sit aspernatur aut odit</p>
</div>

<div class="abs rule"></div>
<div class="abs round" style="left:100px"><svg width="16" height="10" viewBox="0 0 16 10"><path d="M15 5H2M6 1 2 5l4 4" fill="none" stroke="#fff" stroke-width="2"/></svg></div>
<div class="abs round" style="left:150px"><svg width="16" height="10" viewBox="0 0 16 10"><path d="M1 5h13M10 1l4 4-4 4" fill="none" stroke="#fff" stroke-width="2"/></svg></div>
<div class="btn" style="left:893px;top:1117px;width:206px;height:49px">VIEW ALL SOLUTIONS</div>

<!-- who we are -->
<h2 class="abs display section-title" style="top:1244px">Who We Are</h2>
<h3 class="abs who-head">Sed ut perspiciatis unde omn iste natus error sit volupta</h3>
<p class="abs copy" style="left:101px;top:1436px;width:450px">Lorem ipsum dolor sit amet, consectetur adipiscing elit, sed do eiusmod tempor incididunt ut labore et dolore magna aliqua. Ut enim ad minim veniam, quis nostrud exercitation ullamco laboris nisi ut aliquip ex ea commodo consequat. Duis aute irure dolor in reprehenderit in voluptate velit esse cillum dolore eu fugiat nulla pariatur.</p>
<p class="abs copy" style="left:101px;top:1580px;width:450px">Lorem ipsum dolor sit amet, consectetur adipiscing elit, sed do eiusmod tempor incididunt ut labore et dolore magna aliqua. Ut enim ad minim veniam, quis nostrud exercitation ullamco laboris nisi ut aliquip ex ea commodo consequat. Duis aute irure dolor in reprehenderit in voluptate velit esse cillum dolore eu fugiat nulla pariatur.</p>
<div class="btn" style="left:101px;top:1735px;width:175px;height:49px">LEARN MORE</div>
<div class="abs who-photo" role="img" aria-label="Team discussing in a meeting room"></div>
<div class="abs bubble">
  <svg class="abs" style="left:120px;top:36px" width="46" height="34" viewBox="0 0 46 34" fill="#fff"><path d="M0 34V18C0 8 6 2 16 0l2 5c-6 2-9 6-9 11h9v18zM26 34V18c0-10 6-16 16-18l2 5c-6 2-9 6-9 11h9v18z"/></svg>
  Sed ut perspicias unde omnis iste natus error sit voem accusantium doloremque laudantium, totam rem riam, eaque ipsa quae ab illo invtortis et quasi architecto beatae vitae dicta sunt explicabo. Nemo enim ipsam quia voluptas sit aspernatur aut odit Sed ut perspiciatis unde omnis iste natus &nbsp;sit voluptatem
</div>
<div class="abs avatar" role="img" aria-label="Portrait of the quoted team member"></div>
<div class="abs person"><b>Mara Quill</b>Lorem ipsum dolor<br>sit amet, consectetur</div>

<!-- sustainability -->
<div class="abs sus-bg"></div>
<div class="abs sus-img" role="img" aria-label="World map made of green leaves over a recycling symbol"></div>
<h2 class="abs display" style="left:650px;top:1990px;font-size:40px">Sustainability</h2>
<p class="abs copy" style="left:650px;top:2052px;width:445px">Lorem ipsum dolor sit amet, consectetur adipiscing elit, sed do eiusmod tempor incididunt ut labore et dolore magna aliqua. Ut enim ad minim veniam, quis nostrud exercitation ullamco laboris nisi ut aliquip ex ea commodo consequat. Duis aute irure dolor in reprehenderit in voluptate velit esse cillum dolore eu fugiat nulla pariatur.</p>
<p class="abs copy" style="left:650px;top:2190px;width:445px">Lorem ipsum dolor sit amet, consectetur adipiscing elit, sed do eiusmod tempor incididunt ut labore et dolore magna aliqua. Ut enim ad minim veniam, quis nostrud exercitation ullamco laboris nisi ut aliquip ex ea commodo consequat. Duis aute irure dolor in reprehenderit in voluptate velit esse cillum dolore eu fugiat nulla pariatur.</p>
<div class="btn" style="left:650px;top:2343px;width:175px;height:49px">LEARN MORE</div>

<!-- what is lime -->
<section class="abs lime" role="img" aria-label="Limestone quarry rock face tinted blue"></section>
<h2 class="abs display section-title" style="top:2588px;color:#fff">What is Lime?</h2>
<div class="abs lime-copy">Sed ut perspiciatis unde omnis iste natus error sit voluptatem accusantium doloremque laudantium, totam rem aperiam, eaque ipsa quae ab illo inventore Sed ut perspiciatis unde omnis iste natus error sit voluptatem accusantium Sed ut perspiciatis unde omnis iste natus error sit voluptatem</div>
<div class="abs outline-btn">LEARN MORE</div>

<!-- news -->
<h2 class="abs display section-title" style="top:2998px">In The News</h2>
<article class="abs news" style="left:100px">
  <div class="img" role="img" aria-label="Loader working on a quarry hillside" style="background:linear-gradient(180deg,#9fbfd8 0%,#b49a80 50%,#8b6a50 100%)"><span class="date">MAR 2, 2021</span></div>
  <h4>The standard Lm Ipsum passage</h4>
  <p>Lorem ipsum dolor sit amet, contetur adipiscing elit, sed do eiusmod tempor incididunt ut labore et dolore magna aliqua. Ut enim ad minim</p>
  <a>READ MORE »</a>
</article>
<article class="abs news" style="left:438px">
  <div class="img" role="img" aria-label="Glass globe among green ferns" style="background:linear-gradient(180deg,#cfe39a 0%,#7fb449 50%,#3d7a25 100%)"><span class="date">MAR 2, 2021</span></div>
  <h4>The standard Lm Ipsum passage</h4>
  <p>Lorem ipsum dolor sit amet, contetur adipiscing elit, sed do eiusmod tempor incididunt ut labore et dolore magna aliqua. Ut enim ad minim</p>
  <a>READ MORE »</a>
</article>
<article class="abs news" style="left:776px">
  <div class="img" role="img" aria-label="Carbon dioxide lettering with a tree over a field" style="background:linear-gradient(180deg,#4d9ad0 0%,#a9c4cf 55%,#d9a94a 100%)"><span class="date">MAR 2, 2021</span></div>
  <h4>The standard Lm Ipsum passage</h4>
  <p>Lorem ipsum dolor sit amet, contetur adipiscing elit, sed do eiusmod tempor incididunt ut labore et dolore magna aliqua. Ut enim ad minim</p>
  <a>READ MORE »</a>
</article>

<!-- footer -->
<footer class="abs footer"></footer>
<div class="abs f-brand">KESTAL MATERIALS</div>
<div class="abs social" style="left:118px"></div>
<div class="abs social" style="left:156px"></div>
<div class="abs social" style="left:194px"></div>
<div class="abs social" style="left:232px"></div>

<div class="abs f-head" style="left:380px">QUICK LINKS</div>
<div class="abs f-links">Home<br>About<br>FAQ<br>Contact Us</div>

<div class="abs f-head" style="left:552px">CONTACT US</div>
<div class="abs f-contact" style="top:3667px"><i><svg width="10" height="14" viewBox="0 0 10 14"><path d="M5 0a5 5 0 0 0-5 5c0 4 5 9 5 9s5-5 5-9a5 5 0 0 0-5-5zm0 7a2 2 0 1 1 0-4 2 2 0 0 1 0 4z" fill="#fff"/></svg></i><span>48 Ridgeline Road, Hollow Creek<br>20417, United States</span></div>
<div class="abs f-contact" style="top:3731px"><i><svg width="12" height="12" viewBox="0 0 12 12"><path d="M2.5 0 5 3 3.5 4.5c.7 1.6 2.4 3.3 4 4L9 7l3 2.5L10.5 12C5 12 0 7 0 1.5z" fill="#fff"/></svg></i><span>555-014-2290</span></div>
<div class="abs f-contact" style="top:3775px"><i><svg width="12" height="10" viewBox="0 0 12 10"><rect x=".5" y=".5" width="11" height="9" fill="none" stroke="#fff"/><path d="M.5.5 6 5l5.5-4.5" fill="none" stroke="#fff"/></svg></i><span>info@kestalmaterials.com</span></div>

<div class="abs f-head" style="left:825px">SUBSCRIBE TO OUR BLOG</div>
<div class="abs f-sub">Sign up today to get resources on how to attract and retain more customers!</div>
<div class="abs email">
  <svg width="13" height="10" viewBox="0 0 12 10" style="margin-right:8px"><rect x=".5" y=".5" width="11" height="9" fill="none" stroke="#888"/><path d="M.5.5 6 5l5.5-4.5" fill="none" stroke="#888"/></svg>Email Address
</div>
<div class="abs send"><svg width="18" height="18" viewBox="0 0 18 18"><path d="M17 1 1 8l6 2 2 6z" fill="#fff"/></svg></div>

<div class="abs f-rule"></div>
<div class="abs f-legal" style="left:106px">Copyright © 2021 Kestal Materials &nbsp;All Rights Reserved</div>
<div class="abs f-legal" style="left:818px">Terms and Conditions &nbsp;&nbsp;| &nbsp;&nbsp;Privacy Policy</div>

</body>
</html>
```